BUSINESS CARD DESIGN

NAME- DALE VORSKIN
PHONE NUMER - 555- 714-9082
EMAIL- OFFICE@TRV-GROUNDMAKRZ.COM
BACK OF CARD- SPEACIALIZES IN LAND CLEARING, FORESTRY MUCLHING AND EXCAVATION

Contact Information for Business Card

NAME- DALE VORSKIN PHONE NUMER - 555- 714-9082 EMAIL- OFFICE@TRV-GROUNDMAKRZ.COM BACK OF CARD- SPEACIALIZES IN LAND CLEARING , MUCLHING AND EXCAVATION

```html
<!DOCTYPE html>
<html lang="en">
<head>
<meta charset="utf-8">
<title>Traverse Ground Makerz – Business Card</title>
<link rel="stylesheet" href="https://fonts.googleapis.com/css2?family=Montserrat:wght@700;800&display=swap">
<style>
  :root {
    --gold: #F6B31B;
    --ink: #000000;
    --paper: #ffffff;
  }
  * { margin: 0; padding: 0; box-sizing: border-box; }
  html, body {
    width: 1200px; height: 1131px; overflow: hidden;
    background: var(--paper);
    font-family: "Montserrat", sans-serif;
  }
  .card {
    position: absolute; left: 256px; width: 689px; height: 394px;
    background: var(--ink); overflow: hidden;
  }
  .card--front { top: 151px; }
  .card--back { top: 626px; }

  .front-panel { position: absolute; inset: 0; }

  .brand {
    position: absolute; display: flex; flex-direction: column; align-items: center;
    color: var(--gold); font-weight: 800; text-align: center;
  }
  .brand__mark {
    border: 4px solid var(--gold); border-radius: 50%;
  }
  .brand__name { line-height: 1.05; }
  .brand__sub { display: flex; align-items: center; width: 100%; gap: 8px; }
  .brand__sub::before, .brand__sub::after {
    content: ""; flex: 1; height: 2px; background: var(--gold);
  }
  .brand__phone { width: 100%; display: flex; justify-content: space-between; }

  .card--front .brand { left: 46px; top: 82px; width: 206px; }
  .card--front .brand__mark { width: 96px; height: 96px; margin-bottom: 14px; }
  .card--front .brand__name { font-size: 19px; }
  .card--front .brand__sub { font-size: 11px; letter-spacing: 4px; margin: 4px 0 6px; }
  .card--front .brand__phone { font-size: 9px; }

  .card--back .brand { left: 206px; top: 78px; width: 276px; }
  .card--back .brand__mark { width: 126px; height: 126px; margin-bottom: 26px; }
  .card--back .brand__name { font-size: 25px; }
  .card--back .brand__sub { font-size: 14px; letter-spacing: 6px; margin: 6px 0 8px; }
  .card--back .brand__phone { font-size: 11px; }

  .person { position: absolute; left: 373px; top: 103px; color: var(--gold); font-weight: 700; }
  .person__name { font-size: 30px; line-height: 1.1; letter-spacing: -0.3px; }
  .person__role {
    font-size: 21px; line-height: 1.1; display: inline-block; margin-top: 2px;
    padding-bottom: 3px; border-bottom: 3px solid var(--ink); width: 101px;
  }

  .contacts { position: absolute; left: 373px; top: 224px; list-style: none; }
  .contacts__item { display: flex; align-items: center; height: 40px; }
  .contacts__icon { width: 26px; height: 26px; margin-right: 17px; flex: none; }
  .contacts__text { color: var(--gold); font-weight: 700; font-size: 15.5px; letter-spacing: -0.2px; }

  .tagline {
    position: absolute; left: 0; right: 0; top: 345px; text-align: center;
    color: var(--gold); font-weight: 700; font-size: 13.5px; letter-spacing: 1px;
  }
</style>
</head>
<body>

<section class="card card--front" aria-label="Business card front">
  <svg class="front-panel" width="689" height="394" viewBox="0 0 689 394">
    <polygon fill="#ffffff" points="336,0 689,0 689,394 336,394 281.6,337.6 352,268 281.6,200 353.6,128 281.6,56"/>
  </svg>

  <div class="brand">
    <div class="brand__mark"></div>
    <div class="brand__name">TRAVERSE GROUND</div>
    <div class="brand__sub">MAKERZ LLC</div>
    <div class="brand__phone"><span>5</span><span>5</span><span>5</span><span>-</span><span>7</span><span>1</span><span>4</span><span>-</span><span>9</span><span>0</span><span>8</span><span>2</span></div>
  </div>

  <div class="person">
    <div class="person__name">DALE VORSKIN</div>
    <div class="person__role">OWNER</div>
  </div>

  <ul class="contacts">
    <li class="contacts__item">
      <svg class="contacts__icon" viewBox="0 0 26 26"><rect x="1" y="5" width="24" height="16" fill="none" stroke="#000" stroke-width="2"/><polyline points="1,5 13,15 25,5" fill="none" stroke="#000" stroke-width="2"/><line x1="1" y1="21" x2="10" y2="12" stroke="#000" stroke-width="2"/><line x1="25" y1="21" x2="16" y2="12" stroke="#000" stroke-width="2"/></svg>
      <span class="contacts__text">@TRV-GROUNDMAKRZ.COM</span>
    </li>
    <li class="contacts__item">
      <svg class="contacts__icon" viewBox="0 0 26 26"><path d="M6 2 L10 7 L8 10 C9 13 12 17 16 18 L19 16 L24 20 L21 24 C12 24 2 14 2 5 Z" fill="none" stroke="#000" stroke-width="1.6" stroke-linejoin="round"/><path d="M15 6 A6 6 0 0 1 20 11" fill="none" stroke="#000" stroke-width="1.4"/><path d="M15 2 A10 10 0 0 1 24 11" fill="none" stroke="#000" stroke-width="1.4"/></svg>
      <span class="contacts__text">+555- 714-9082</span>
    </li>
    <li class="contacts__item">
      <svg class="contacts__icon" viewBox="0 0 26 26"><circle cx="13" cy="13" r="11" fill="none" stroke="#000" stroke-width="1.8"/><ellipse cx="13" cy="13" rx="5" ry="11" fill="none" stroke="#000" stroke-width="1.5"/><line x1="2" y1="13" x2="24" y2="13" stroke="#000" stroke-width="1.5"/><line x1="4" y1="7.5" x2="22" y2="7.5" stroke="#000" stroke-width="1.3"/><line x1="4" y1="18.5" x2="22" y2="18.5" stroke="#000" stroke-width="1.3"/></svg>
      <span class="contacts__text">WWW.TRV-GROUNDMAKRZ.COM</span>
    </li>
  </ul>
</section>

<section class="card card--back" aria-label="Business card back">
  <div class="brand">
    <div class="brand__mark"></div>
    <div class="brand__name">TRAVERSE GROUND</div>
    <div class="brand__sub">MAKERZ LLC</div>
    <div class="brand__phone"><span>5</span><span>5</span><span>5</span><span>-</span><span>7</span><span>1</span><span>4</span><span>-</span><span>9</span><span>0</span><span>8</span><span>2</span></div>
  </div>
  <p class="tagline">SPEACIALIZES IN LAND CLEARING , MUCLHING AND EXCAVATION</p>
</section>

</body>
</html>
```